New Business Card Design Project

We require a business card design for Vexalund, a newly established Indian company.
Our focus is on the development, manufacturing, and export of a diverse array of pharmaceutical products on a global scale. The card should convey a professional appearance, as our primary markets are in Africa, China, and Southeast Asian nations.
We envision a two-sided business card, with the reverse side dedicated to a logo set against a solid color or an elegantly designed pattern. The corners should be rounded. We would appreciate seeing both horizontal and vertical design options. We trust the designer to utilize their expertise in creating this design.

The content for the business card is included in the attached Word file.

Target Market(s)

Our primary markets are in Africa, China, and Southeast Asian, Latin America, Maldives, Sri Lanka

Industry/Entity Type

Pharmaceutical Manufacturing and Export

Contact Information for Business Card

Colors

Designer to choose colors to be used in the design.

Requirements
Must have
• The reverse side of the business card features solely the logo along with the tagline, "Care Across Borders."
Should not have
• The logo should not exceed two instances, encompassing both the front and back sides of the card.

```html
<!DOCTYPE html>
<html lang="en">
<head>
<meta charset="utf-8">
<title>Vexalund Business Card</title>
<link rel="stylesheet" href="https://fonts.googleapis.com/css2?family=Open+Sans:wght@400;600;700&display=swap">
<style>
  :root {
    --stage: #2e2e30;
    --card: #ffffff;
    --card-shade: #eeeeee;
    --brand-blue: #2196cc;
    --brand-red: #d9533f;
    --ink: #3a3a3a;
    --radius: 30px;
  }
  * { margin: 0; padding: 0; box-sizing: border-box; }
  html, body {
    width: 1200px; height: 900px; overflow: hidden;
    background: var(--stage);
    font-family: "Open Sans", Arial, sans-serif;
  }
  .stage { position: relative; width: 1200px; height: 900px; }
  .card {
    position: absolute; left: 280px;
    width: 640px; height: 366px;
    border-radius: var(--radius);
    background: linear-gradient(120deg, var(--card-shade) 0%, var(--card) 60%);
    box-shadow: 0 14px 30px rgba(0,0,0,.45);
    overflow: hidden;
  }
  .card--back { top: 60px; }
  .card--front { top: 474px; }

  .wordmark {
    display: flex; align-items: center; gap: 12px;
    font-weight: 700; color: var(--brand-blue);
    letter-spacing: .5px; line-height: 1; white-space: nowrap;
  }
  .wordmark__dot {
    width: 22px; height: 22px; border-radius: 50%;
    background: var(--brand-red);
  }

  .card--back .brand-block { position: absolute; left: 70px; bottom: 70px; }
  .card--back .wordmark { font-size: 62px; }
  .card--back .wordmark__dot { width: 28px; height: 28px; }
  .brand-rule {
    height: 2px; width: 360px; margin: 14px 0 10px;
    background: var(--brand-red);
  }
  .tagline {
    font-weight: 600; font-size: 22px; letter-spacing: 2px;
    color: var(--brand-blue); padding-left: 40px; white-space: nowrap;
  }

  .card--front .wordmark { position: absolute; left: 60px; top: 70px; font-size: 44px; }
  .person {
    position: absolute; left: 60px; bottom: 48px;
    color: var(--ink); font-size: 17px; line-height: 1.35;
  }
  .person__name {
    color: var(--brand-blue); font-weight: 700;
    font-size: 20px; letter-spacing: .5px;
  }
  .contact {
    position: absolute; right: 44px; bottom: 56px;
    list-style: none; color: var(--ink); font-size: 15px;
  }
  .contact li { display: flex; align-items: center; gap: 10px; margin-top: 7px; white-space: nowrap; }
  .contact svg { width: 16px; height: 16px; flex: none; }
</style>
</head>
<body>
<main class="stage">

  <section class="card card--back" aria-label="Card reverse">
    <div class="brand-block">
      <div class="wordmark"><span class="wordmark__dot"></span>Vexalund</div>
      <div class="brand-rule"></div>
      <div class="tagline">CARE ACROSS BORDERS</div>
    </div>
  </section>

  <section class="card card--front" aria-label="Card front">
    <div class="wordmark"><span class="wordmark__dot"></span>Vexalund</div>

    <div class="person">
      <div class="person__name">ROHAN K. DESAI</div>
      <div>CEO</div>
      <div>Vexalund</div>
    </div>

    <ul class="contact">
      <li>
        <svg viewBox="0 0 16 16" fill="none" stroke="#2196cc" stroke-width="1.5"><rect x="4" y="1" width="8" height="14" rx="1.5"/><line x1="7" y1="12.5" x2="9" y2="12.5"/></svg>
        +919812345670
      </li>
      <li>
        <svg viewBox="0 0 16 16"><rect x="1" y="3" width="14" height="10" rx="1" fill="#2196cc"/><path d="M1.5 3.5 8 9l6.5-5.5" fill="none" stroke="#fff" stroke-width="1.3"/></svg>
        rdesai@vexalund.com
      </li>
      <li>
        <svg viewBox="0 0 16 16" fill="none" stroke="#2196cc" stroke-width="1.3"><circle cx="8" cy="8" r="6.5"/><ellipse cx="8" cy="8" rx="3" ry="6.5"/><line x1="1.5" y1="8" x2="14.5" y2="8"/></svg>
        www.vexalund.com
      </li>
      <li>
        <svg viewBox="0 0 16 16"><path d="M8 1a5 5 0 0 0-5 5c0 3.6 5 9 5 9s5-5.4 5-9a5 5 0 0 0-5-5z" fill="#2196cc"/><circle cx="8" cy="6" r="2" fill="#fff"/></svg>
        12, Lotus Colony, Nagpur, 440010, India
      </li>
    </ul>
  </section>

</main>
</body>
</html>
```